The design should look similar to the uploaded example to accommodate the information needed for a business card template. I would like to see the colors orange and charcoal grey incorporated along with the logo.The following should be on the back of the card SPECIALIZING IN NEW AND USED TIRES & WHEELS FOR:- Loaders- Skid Steers- Telehandlers- Boom Lifts- Forklifs and moreELIMINATING DOWNTIMEWheel Exchange Program for New & Used Foam Filled and Solid Rubber TiresSPECIALTY SERVICES- Foam Filling Tires- Largest Tire Press in SE- ONSITE Forklift Tire Press- Boom Truck Services - Rubber Tracks

Target Market(s)

New and Existing Customers

Industry/Entity Type

Business

Contact Information for Business Card

NAMEHEAVY DUTY TIRE, LLC8470 Belvedere RoadWest Palm Beach, FL 33411P: 844-HD-TIRESF: 561-431-6469C:E: W: WWW.GRANITERIMSUPPLY-EXAMPLE.COM

Font styles to use
Sans Serif

Colors
f37122
333333

Requirements
Must have
• The logo and the information indicated for the backside of the card
Nice to have
• Keep the orange and charcoal grey colors

```html
<!DOCTYPE html>
<html lang="en">
<head>
<meta charset="utf-8">
<title>Granite Rim Supply – Business Card</title>
<link href="https://fonts.googleapis.com/css2?family=Source+Sans+3:wght@400;600;700&display=swap" rel="stylesheet">
<style>
  :root {
    --orange: #f37122;
    --charcoal: #3a4849;
    --text-light: #f2f2f2;
    --backdrop: #e9e6e1;
  }
  * { box-sizing: border-box; margin: 0; padding: 0; }
  html, body { width: 1200px; height: 900px; overflow: hidden; }
  body {
    background: var(--backdrop);
    font-family: "Source Sans 3", Arial, sans-serif;
    display: flex;
    flex-direction: column;
    align-items: center;
    justify-content: center;
    gap: 40px;
  }
  .card {
    width: 700px;
    height: 400px;
    background: var(--charcoal);
    color: var(--text-light);
    position: relative;
    box-shadow: 0 6px 18px rgba(0,0,0,.25);
  }

  /* Back side */
  .card-back { display: grid; grid-template-columns: 1fr 1fr; padding: 60px 40px 0; column-gap: 40px; }
  .heading {
    color: var(--orange);
    font-weight: 700;
    font-size: 21px;
    line-height: 1.1;
    text-transform: uppercase;
    margin-bottom: 12px;
  }
  .services { text-align: right; padding-top: 22px; }
  .services li, .equipment li {
    list-style: none;
    font-size: 18px;
    font-weight: 600;
    line-height: 1.3;
  }
  .services li::after {
    content: ""; display: inline-block; width: 7px; height: 7px; border-radius: 50%;
    background: var(--orange); margin-left: 10px; vertical-align: middle;
  }
  .equipment li { font-size: 16px; font-weight: 400; }
  .equipment li::before {
    content: ""; display: inline-block; width: 7px; height: 7px; border-radius: 50%;
    background: var(--orange); margin-right: 8px; vertical-align: middle;
  }
  .downtime { grid-column: 1 / span 2; text-align: center; margin-top: 26px; }
  .downtime .heading { margin-bottom: 4px; }
  .downtime p { font-size: 18px; font-weight: 600; line-height: 1.2; }

  /* Front side */
  .card-front { display: flex; align-items: center; padding: 0 40px 0 60px; gap: 50px; }
  .brand { display: flex; flex-direction: column; align-items: center; gap: 16px; width: 260px; }
  .brand-dot { width: 170px; height: 170px; border-radius: 50%; background: var(--orange); }
  .brand-name { color: var(--orange); font-weight: 700; font-size: 30px; letter-spacing: 1px; }
  .contact { flex: 1; }
  .contact-name { color: var(--orange); font-size: 24px; font-weight: 600; }
  .company { color: var(--orange); font-size: 18px; font-weight: 600; margin-bottom: 6px; }
  .address { font-size: 16px; line-height: 1.35; margin-bottom: 16px; }
  .lines { list-style: none; }
  .lines li { display: flex; align-items: center; gap: 12px; font-size: 16px; line-height: 1.55; }
  .lines svg { width: 14px; height: 14px; fill: var(--orange); flex: none; }
</style>
</head>
<body>

<section class="card card-back" aria-label="Card back">
  <div class="services">
    <h2 class="heading">Specialty Services</h2>
    <ul>
      <li>Foam Filling Tires</li>
      <li>Largest Tire Press in SE</li>
      <li>ONSITE Forklift Tire Press</li>
      <li>Boom Truck Services</li>
      <li>Rubber Tracks</li>
    </ul>
  </div>
  <div class="equipment">
    <h2 class="heading">Specializing in new and used tires &amp; wheels for:</h2>
    <ul>
      <li>Loaders</li>
      <li>Skid Steers</li>
      <li>Telehandlers</li>
      <li>Boom Lifts</li>
      <li>Forklifs and more</li>
    </ul>
  </div>
  <div class="downtime">
    <h2 class="heading">Eliminating Downtime</h2>
    <p>Wheel Exchange Program for New &amp; Used Foam<br>Filled and Solid Rubber Tires</p>
  </div>
</section>

<section class="card card-front" aria-label="Card front">
  <div class="brand">
    <div class="brand-dot"></div>
    <div class="brand-name">GRANITE RIM</div>
  </div>
  <div class="contact">
    <div class="contact-name">Marcus Delane</div>
    <div class="company">GRANITE RIM SUPPLY, LLC</div>
    <div class="address">5126 Marston Lane<br>Harbor Point, FL 33420</div>
    <ul class="lines">
      <li><svg viewBox="0 0 16 16" aria-hidden="true"><path d="M3 1h3l1.5 4-2 1.3a9 9 0 0 0 4.2 4.2L11 8.5l4 1.5v3a2 2 0 0 1-2 2A13 13 0 0 1 1 3a2 2 0 0 1 2-2z"/></svg>844-GR-WHEEL</li>
      <li><svg viewBox="0 0 16 16" aria-hidden="true"><path d="M4 1h7v4H4zM1 6h14v7h-3v2H4v-2H1zm4 5v3h6v-3z"/></svg>561-278-9053</li>
      <li><svg viewBox="0 0 16 16" aria-hidden="true"><path d="M4 0h8a1 1 0 0 1 1 1v14a1 1 0 0 1-1 1H4a1 1 0 0 1-1-1V1a1 1 0 0 1 1-1zm1 2v10h6V2zm3 11a1 1 0 1 0 0 2 1 1 0 0 0 0-2z"/></svg>123-456-7890</li>
      <li><svg viewBox="0 0 16 16" aria-hidden="true"><path d="M1 3h14v10H1zm1.5 1.5L8 9l5.5-4.5z" fill-rule="evenodd"/></svg>info@graniterimsupply-example.com</li>
      <li><svg viewBox="0 0 16 16" aria-hidden="true"><circle cx="8" cy="8" r="7"/></svg>www.graniterimsupply-example.com</li>
    </ul>
  </div>
</section>

</body>
</html>
```